Heritage Hollow Business Cards

Require a business card design. <br/><br/>Needs to include logo (either round or long version) plus these details:<br/>Maya Torvell<br/>Heritage Hollow<br/>maya@kelvadtrading.com.au<br/>02 6481 7395<br/>PO Box Glenwarra NSW 2791<br/>www.heritagehollow.com.au<br/><br/>I need in an editable format so that I can create for multiple staff members. <br/><br/>

Target Market(s)

We are an online store selling renovation products to home owners are builders. Looking for a classic classy design.

Industry/Entity Type

Home And Garden

Contact Information for Business Card

Maya Torvell
Heritage Hollow
maya@kelvadtrading.com.au
02 6481 7395
PO Box Glenwarra NSW 2791
www.heritagehollow.com.au

Colors

Designer to choose colors to be used in the design.

Requirements
Must have
• Must include Logo.

```html
<!DOCTYPE html>
<html lang="en">
<head>
<meta charset="utf-8">
<title>Heritage Hollow Business Cards</title>
<link href="https://fonts.googleapis.com/css2?family=Alegreya:wght@500&family=Roboto:wght@300;400;700&display=swap" rel="stylesheet">
<style>
  :root{
    --page:#dcdde1;
    --card-front:#666667;
    --card-back:#ececec;
    --ink-dark:#2f2f30;
    --ink:#1e1e1e;
    --ink-soft:#444;
    --rule:#7a7a7a;
  }
  *{margin:0;padding:0;box-sizing:border-box}
  html,body{width:1200px;height:1200px;overflow:hidden;background:var(--page)}
  .canvas{position:relative;width:1200px;height:1200px}
  .card{position:absolute;left:271px;width:659px;height:378px;border-radius:14px;overflow:hidden}
  .card--front{top:180px;background:var(--card-front)}
  .card--back{top:643px;background:var(--card-back)}
  .brand-lockup{position:absolute;left:0;right:0;top:128px;display:flex;align-items:center;justify-content:center;gap:16px}
  .brand-mark{width:34px;height:34px;border:2px solid var(--ink-dark);border-radius:50%}
  .brand-name{font-family:'Alegreya',serif;font-weight:500;font-size:58px;color:var(--ink-dark);letter-spacing:1px;line-height:1}
  .contact{position:absolute;left:93px;top:125px;width:200px;text-align:center;font-family:'Roboto',sans-serif;color:var(--ink-soft)}
  .contact__name{font-family:'Alegreya',serif;font-weight:500;font-size:28px;color:var(--ink);letter-spacing:.5px;line-height:1;text-transform:uppercase}
  .contact__rule{width:143px;height:1px;background:var(--rule);margin:6px auto}
  .contact__company{font-size:16px;font-weight:400;color:var(--ink);margin-top:8px}
  .contact__address{font-size:12.5px;font-weight:300;margin-top:2px;white-space:nowrap}
  .contact__line{display:flex;align-items:center;justify-content:center;gap:4px;font-size:12.5px;font-weight:300;margin-top:4px;white-space:nowrap}
  .contact__line svg{width:10px;height:10px;flex:none}
  .contact__line b{font-weight:700}
</style>
</head>
<body>
<div class="canvas">
  <section class="card card--front">
    <div class="brand-lockup">
      <span class="brand-mark"></span>
      <span class="brand-name">Heritage Hollow</span>
    </div>
  </section>

  <section class="card card--back">
    <div class="contact">
      <p class="contact__name">Maya Torvell</p>
      <div class="contact__rule"></div>
      <p class="contact__company">Heritage Hollow</p>
      <p class="contact__address">PO Box Glenwarra NSW 2791</p>
      <div class="contact__rule"></div>
      <p class="contact__line">
        <svg viewBox="0 0 10 10"><path d="M2 1l2 2-1 1.2c.6 1.2 1.5 2.1 2.8 2.8L7 6l2 2-1.3 1.3C4.5 9 1 5.5.7 2.3z" fill="#333"/></svg>
        02 6481 7395
      </p>
      <p class="contact__line">
        <svg viewBox="0 0 10 10"><rect x=".5" y="2" width="9" height="6.5" fill="#333"/><path d="M.5 2l4.5 3.5L9.5 2" stroke="#eee" stroke-width=".8" fill="none"/></svg>
        maya@kelvadtrading.com.au
      </p>
      <p class="contact__line">
        <svg viewBox="0 0 10 10"><circle cx="5" cy="5" r="4.4" fill="none" stroke="#333" stroke-width=".9"/><ellipse cx="5" cy="5" rx="2" ry="4.4" fill="none" stroke="#333" stroke-width=".8"/><path d="M.6 5h8.8M1.3 3h7.4M1.3 7h7.4" stroke="#333" stroke-width=".7"/></svg>
        www.<b>heritagehollow</b>.com.au
      </p>
    </div>
  </section>
</div>
</body>
</html>
```